Restyle corporate identity (+ logo) for a road construction company

We need a new logo and stationary design for our company VARNOK path. VARNOK path® increases the road base strength, while reducing major costs and time of road construction. Attached some examples of the current design.

Our wishes for the new logo:
- Business look
- Style sheet
- Modern

More information: www.varnokpath.example
Updates

Target Market(s)

Government

Industry/Entity Type

Construction

Requirements
Must have
• Logo (with road sign) + text

```html
<!DOCTYPE html>
<html lang="en">
<head>
<meta charset="utf-8">
<title>VARNOK path – Business Card</title>
<link rel="stylesheet" href="https://fonts.googleapis.com/css2?family=Source+Sans+3:wght@400;600&display=swap">
<style>
  :root {
    --brand-blue: #1a82e6;
    --paper: #eef0f2;
    --panel: #eef0f3;
    --ink-white: #ffffff;
    --backdrop: #8c8c8c;
  }
  * { margin: 0; padding: 0; box-sizing: border-box; }
  html, body { width: 1105px; height: 1200px; overflow: hidden; }
  body {
    background: var(--backdrop);
    font-family: "Source Sans 3", sans-serif;
    position: relative;
  }
  .card {
    position: absolute;
    left: 182px;
    width: 747px;
    height: 427px;
    box-shadow: 0 6px 14px rgba(0,0,0,0.25);
  }
  .card--front { top: 119px; background: var(--brand-blue); color: var(--ink-white); }
  .card--back { top: 636px; background: var(--paper); }

  .holder { position: absolute; left: 51px; top: 50px; }
  .holder__name { font-size: 26px; font-weight: 600; letter-spacing: 0.5px; line-height: 1.2; }
  .holder__role { font-size: 20px; font-weight: 400; line-height: 1.3; }

  .address { position: absolute; left: 51px; top: 210px; font-size: 20px; line-height: 26px; }

  .contacts { position: absolute; left: 51px; top: 303px; list-style: none; font-size: 20px; }
  .contacts li { display: flex; align-items: center; height: 28px; }
  .contacts svg { width: 17px; height: 17px; margin-right: 12px; fill: var(--ink-white); }

  .logo-panel {
    position: absolute;
    left: 342px; top: 25px;
    width: 381px; height: 385px;
    border-radius: 48px;
    background: var(--panel);
    display: flex; align-items: center; justify-content: center;
  }
  .wordmark {
    font-family: "Source Sans 3", sans-serif;
    font-weight: 600;
    color: var(--brand-blue);
    letter-spacing: 2px;
    line-height: 1;
  }
  .logo-panel .wordmark { font-size: 54px; }
  .card--back .wordmark-row {
    position: absolute; inset: 0;
    display: flex; align-items: center; justify-content: center; gap: 18px;
  }
  .wordmark-square { width: 44px; height: 44px; background: var(--brand-blue); border-radius: 8px; }
  .card--back .wordmark { font-size: 60px; }
</style>
</head>
<body>
  <section class="card card--front">
    <div class="holder">
      <p class="holder__name">MAREN VOLT</p>
      <p class="holder__role">CEO/Founder</p>
    </div>
    <address class="address" style="font-style:normal">
      Lindqvist Kade 58<br>
      4120 KP Veldhaven<br>
      The Netherlands
    </address>
    <ul class="contacts">
      <li>
        <svg viewBox="0 0 24 24" aria-hidden="true"><path d="M6.6 10.8a15.1 15.1 0 0 0 6.6 6.6l2.2-2.2c.3-.3.7-.4 1-.2 1.1.4 2.3.6 3.6.6.6 0 1 .4 1 1V20c0 .6-.4 1-1 1A17 17 0 0 1 3 4c0-.6.4-1 1-1h3.5c.6 0 1 .4 1 1 0 1.3.2 2.5.6 3.6.1.3 0 .7-.2 1z"/></svg>
        555 014 2290
      </li>
      <li>
        <svg viewBox="0 0 24 24" aria-hidden="true"><path d="M2 5h20v14H2z M3 6l9 7 9-7" fill="none" stroke="#fff" stroke-width="2"/></svg>
        info@varnokpath.example
      </li>
      <li>
        <svg viewBox="0 0 24 24" aria-hidden="true"><circle cx="12" cy="12" r="10" fill="none" stroke="#fff" stroke-width="2"/><path d="M2 12h20M12 2c3 3 3 17 0 20M12 2c-3 3-3 17 0 20" fill="none" stroke="#fff" stroke-width="1.6"/></svg>
        www.varnokpath.example
      </li>
    </ul>
    <div class="logo-panel">
      <span class="wordmark">VARNOK path</span>
    </div>
  </section>

  <section class="card card--back">
    <div class="wordmark-row">
      <span class="wordmark-square"></span>
      <span class="wordmark">VARNOK path</span>
    </div>
  </section>
</body>
</html>
```